Fine Art business needs new website

We need a simple website with a home page, about us page, New sculptures, Sold sculptures, and a contact us page.Our sculptures are very high end one of a kind pieces. As such we need the site to be VERY elegant and professional. Lastly, because I'll be updating pictures on the website on a monthly basis it needs to be user friendly to update (Wordpress is preferred). The only branding we have so far for the business is a business card.
Updates
I wasn't completely ready when this project launched, also I am on the road right now and haven't been able to be as responsive to all you designers as I would like. I will work on giving feedback to all the top designs we've received so far. Thank you all so much for your participation and hardwork.
Target Market(s)
High end customers (affluent), art collectors, interior decorators/designers
Industry/Entity Type
Art Gallery
Coding
Coded - Design and coding required
Number of Pages Required
5+ page
Requirements
Must have
- Easily editable picture gallery for myself so that I can add new pieces(pictures of the pieces), remove sold pieces, etc. I would like the website to be built in wordpress so I can update it. I currently use mangewordpress through Netmarro for my other business website and would like to do the same for this one.
- Pages:
- -Intro page with featured pieces
- -Current pieces gallery (for sale) mainly a picture gallery
- -Sculptures archive (sold pieces) another picture gallery
- -About us: Pull-down of -about the artist (attached content)
- -Artistic Process (attached content)
- -Show Schedule:
- -one page dedicated to "friends of TMV" (basically a link page)
- TO BE CLEAR "www.pineroverslane.com" IS A TOTALLY DIFFERENT SITE AND I'M NOT TRYING TO COMBINE THE TWO OR JOIN THEM INTO ONE. This page needs be more elegant and seperate from The Pine Rovers site.
- UPDATE: I'd like a link to the TMV Plume page: https://www.faceplume-social.com/mirelcraftworks/
Nice to have
- I would like the pictures on the gallery pages able to have text connected with them (Materials, price)
- I would like the site style and fonts to be similar to our business cards we've already had designed (picture attached).
Should not have
- Too much flash or other things that will make the site slow to load.

```html
<!DOCTYPE html>
<html lang="en">
<head>
<meta charset="utf-8">
<title>About Us</title>
<link href="https://fonts.googleapis.com/css2?family=Lato:wght@400;700&family=EB+Garamond:wght@400;500&display=swap" rel="stylesheet">
<style>
:root{
  --bar:#262626;
  --page:#efefef;
  --band:#f7f7f7;
  --ink:#2b2b2b;
  --body:#3a3a3a;
  --white:#ffffff;
  --tab-dark:#111111;
  --tab-mid:#4a4a4a;
  --rule:#c9c9c9;
}
*{box-sizing:border-box;margin:0;padding:0}
html,body{width:740px;height:1200px;overflow:hidden}
body{position:relative;background:var(--page);font-family:"Lato",sans-serif;color:var(--ink)}
.abs{position:absolute}
.topbar{left:0;top:0;width:740px;height:46px;background:var(--bar);box-shadow:0 2px 4px rgba(0,0,0,.25)}
.nav{left:116px;top:17px;display:flex;gap:13px;font-size:8.5px;color:var(--white);letter-spacing:.2px}
.nav .active{border-bottom:1px solid #8a9fc4;padding-bottom:3px;display:flex;align-items:center;gap:4px}
.menu-icon{left:602px;top:17px}
.dropdown{left:116px;top:36px;width:79px;height:38px;background:var(--white);box-shadow:1px 1px 3px rgba(0,0,0,.3);font-size:7px;padding:4px 0 0 12px;line-height:17px}
.dots{left:599px;top:74px}
.page-title{left:0;width:740px;top:94px;text-align:center;font-size:28px;font-weight:700;letter-spacing:.3px}
.tabs{left:513px;top:96px;width:106px}
.tab{height:26px;font-size:9px;display:flex;align-items:center;padding-left:17px}
.tab-current{background:var(--tab-dark);color:var(--white);font-weight:700}
.tab-other{background:var(--tab-mid);color:#cfcfcf;height:25px;padding-left:19px}
.section-title{left:0;width:740px;top:172px;text-align:center;font-size:17px;font-weight:700}
.section-rule{left:318px;top:199px;width:105px;height:2px;background:var(--rule)}
.photo{background:linear-gradient(135deg,#7d7a70,#4b5e84 60%,#2f4fa0);box-shadow:2px 2px 4px rgba(0,0,0,.3)}
.team-photo{left:257px;top:224px;width:226px;height:170px}
.story{left:156px;width:428px;top:411px;text-align:center;font-size:10.4px;line-height:16px;color:var(--body)}
.story p{margin-bottom:15px}
.band{left:0;top:694px;width:740px;height:349px;background:var(--band)}
.artist-name{font-size:14px;font-weight:400;color:var(--ink)}
.name-left{left:117px;top:718px}
.name-right{right:117px;top:867px}
.portrait-left{left:117px;top:745px;width:170px;height:116px;background:linear-gradient(160deg,#8d8a7a,#5a4c3c 55%,#2a2a28)}
.portrait-right{left:455px;top:901px;width:169px;height:116px;background:linear-gradient(180deg,#c9b9a8,#7a6a5c 50%,#e4e6ea)}
.bio{font-family:"EB Garamond",serif;color:var(--body);font-size:10.2px;line-height:16px}
.bio h3{font-weight:500;font-size:11px;margin-bottom:5px;color:var(--ink)}
.bio-left{left:305px;top:777px;width:290px}
.bio-right{left:150px;top:935px;width:292px;text-align:right}
.bio-right h3{padding-right:7px}
.footer{left:0;top:1070px;width:740px;height:130px;background:var(--bar);color:var(--white)}
.foot-head{font-size:13.5px;font-weight:700;top:25px}
.foot-about{left:122px}
.foot-about p{font-size:7.4px;line-height:13.3px;margin-top:6px;font-weight:400}
.foot-address{left:325px}
.contact-list{list-style:none;font-size:7.4px;margin-top:6px;font-weight:400}
.contact-list li{display:flex;align-items:center;gap:6px;height:13.3px}
.contact-list .cta{font-weight:700;padding-left:14px}
.foot-social{right:116px;text-align:right}
.social-links{display:flex;gap:6px;justify-content:center;margin-top:7px;font-size:7.4px;font-weight:400;color:#d6d6d6}
</style>
</head>
<body>
<header class="abs topbar">
  <nav class="abs nav">
    <span>HOME</span>
    <span class="active">ABOUT
      <svg width="7" height="5" viewBox="0 0 7 5"><path d="M.5 .8 3.5 3.8 6.5 .8" fill="none" stroke="#fff" stroke-width=".8"/></svg>
    </span>
    <span>GALLERY</span>
    <span>CONTACT</span>
  </nav>
  <svg class="abs menu-icon" width="22" height="13" viewBox="0 0 22 13" aria-label="Menu">
    <rect y="0" width="22" height="1.8" fill="#fff"/><rect y="5.5" width="22" height="1.8" fill="#fff"/><rect y="11" width="22" height="1.8" fill="#fff"/>
  </svg>
</header>
<div class="abs dropdown"><div>About the Artists</div><div>The Pine Rovers</div></div>

<svg class="abs dots" width="20" height="5" viewBox="0 0 20 5"><circle cx="2.5" cy="2.5" r="2" fill="#222"/><circle cx="10" cy="2.5" r="2" fill="#222"/><circle cx="17.5" cy="2.5" r="2" fill="#222"/></svg>
<h1 class="abs page-title">ABOUT US</h1>
<div class="abs tabs">
  <div class="tab tab-current">Meet The Artists</div>
  <div class="tab tab-other">Artistic Process</div>
</div>

<h2 class="abs section-title">MEET THE ARTISTS</h2>
<div class="abs section-rule"></div>
<div class="abs photo team-photo" role="img" aria-label="Photo of the two artists in the workshop wearing respirator masks"></div>

<div class="abs story">
  <p>Hale Mercer has been mastering the Lapidary Arts since the late 1980’s. Somewhere in the middle of this new career of his he recruited his kids into the shop to help him with the ever increasing demand for his one of a kind fossil and mineral sculptures. An unintended (or possibly intended) consequence of bringing his children into the fold is they eventually fell in love with rocks and became proficient in many of the lapidary techniques.</p>
  <p>Fast forward to 2012, after graduating college and working several years in<br>the real world two of Hale’s children, Corbin and Lenna, decided to work with their Father full-time as a chance to be closer to family while at the same time seeing different parts of the US. Through the past 6 years all of Hale’s children have continued to contribute to the family livelihood on a part-time basis with the exception of Corby who is now a full time Artist alongside his Father.</p>
  <p>Both Hale and Corby have their own unique styles, yet<br>on occasion they will combine their talents to create a collaborative masterpiece.</p>
</div>

<section class="abs band"></section>
<h3 class="abs artist-name name-left">Warren “Hale” Mercer</h3>
<div class="abs photo portrait-left" role="img" aria-label="Portrait of Warren Hale Mercer outdoors in a brown hat"></div>
<div class="abs bio bio-left">
  <h3>Biography</h3>
  <p>“To learn more about the process of creating these one-of-a-kind<br>sculptures please visit the Artistic process page of the website.”</p>
</div>
<h3 class="abs artist-name name-right">Corby Mercer</h3>
<div class="abs bio bio-right">
  <h3>Biography</h3>
  <p>“To learn more about the process of creating these one-of-a-kind<br>sculptures please visit the Artistic process page of the website.”</p>
</div>
<div class="abs photo portrait-right" role="img" aria-label="Portrait of Corby Mercer in a snowy winter setting"></div>

<footer class="abs footer">
  <div class="abs foot-head foot-about">ABOUT US
    <p>This is a dummy text just<br>to provide text in the About Us<br>section which will be added correctly<br>later on.</p>
  </div>
  <div class="abs foot-head foot-address">OUR ADDRESS
    <ul class="contact-list">
      <li><svg width="8" height="8" viewBox="0 0 8 8"><path d="M1.5.5 3 2.3 2.3 3.3C2.8 4.4 3.6 5.2 4.7 5.7L5.7 5 7.5 6.5 6.7 7.5C3.5 7.2.8 4.5.5 1.3Z" fill="#fff"/></svg>(555) 013-2748</li>
      <li><svg width="9" height="7" viewBox="0 0 9 7"><rect x=".4" y=".4" width="8.2" height="6.2" fill="none" stroke="#fff" stroke-width=".8"/><path d="M.4 .4 4.5 4 8.6 .4" fill="none" stroke="#fff" stroke-width=".8"/></svg>corby@pinerovers.com</li>
      <li><svg width="8" height="8" viewBox="0 0 8 8"><path d="M3.2 4.8 4.8 3.2M2.5 3.5 1.3 4.7a1.4 1.4 0 0 0 2 2L4.5 5.5M5.5 4.5 6.7 3.3a1.4 1.4 0 0 0-2-2L3.5 2.5" fill="none" stroke="#fff" stroke-width=".8"/></svg>www.mirelcraftstudio.com</li>
      <li class="cta">CONTACT US</li>
    </ul>
  </div>
  <div class="abs foot-head foot-social">KEEP IN TOUCH
    <div class="social-links"><span>Chirp</span><span>Pinly</span><span>Plume</span><span>Snapgram</span></div>
  </div>
</footer>
</body>
</html>
```